Halvick Ledgers & Advisory Tri-Fold Brochure (8.5"x11")

I need a professional looking brochure for my bookkeeping business. I am looking for something professional yet casual (not too corporate looking). I have attached a sample brochure that will outline the areas and a copy of our logo. I'd like to stick with shades of blue. The final product should communicate professional and personal.

Target Market(s)

Small service businesses.

Industry/Entity Type

Business

Font styles to use
Sans Serif

Requirements
Must have
• Professional looking photos of people in areas where it asks for a picture.

```html
<!DOCTYPE html>
<html lang="en">
<head>
<meta charset="utf-8">
<title>Halvick Ledgers &amp; Advisory – Tri-Fold Brochure</title>
<link rel="stylesheet" href="https://fonts.googleapis.com/css2?family=Marcellus+SC&family=Tinos:ital,wght@0,400;0,700;1,400&display=swap">
<style>
  :root{
    --ink-dark:#2a2a2c;
    --ink-mid:#3a3a3d;
    --blue-bright:#1fa3e6;
    --blue-mid:#1a78c8;
    --blue-deep:#0c3f86;
    --blue-soft:#8fd0ff;
    --paper:#f4f4f4;
    --text-light:#ffffff;
    --text-dark:#222222;
    --stage:#e6e6e6;
  }
  *{box-sizing:border-box;margin:0;padding:0}
  html,body{width:797px;height:1200px;overflow:hidden}
  body{background:var(--stage);font-family:"Tinos",serif;position:relative}
  .sheet{position:absolute;left:47px;width:703px;overflow:hidden;box-shadow:0 2px 8px rgba(0,0,0,.35)}
  .sheet--outside{top:30px;height:547px}
  .sheet--inside{top:612px;height:548px}
  .sheet svg.art{position:absolute;inset:0;width:100%;height:100%}
  .t{position:absolute}
  .caps{font-family:"Marcellus SC",serif;letter-spacing:.5px}
  .pill{position:absolute;background:linear-gradient(var(--blue-bright),var(--blue-mid));color:var(--text-light);border-radius:0 16px 16px 0;font-family:"Marcellus SC",serif;padding-left:28px;line-height:32px;box-shadow:0 2px 4px rgba(0,0,0,.4)}
  .body-copy{font-size:10.5px;line-height:11.6px;text-align:justify}
  .light{color:var(--text-light)}
  .dark{color:var(--text-dark)}
  .blue{color:var(--blue-bright)}
  .soft{color:var(--blue-soft)}
  .navy{color:var(--blue-deep)}
  .list{list-style:none;font-size:10px;line-height:18px}
  .list li{position:relative;padding-left:14px}
  .list li::before{content:"";position:absolute;left:0;top:5px;width:7px;height:7px;border-radius:50%;background:var(--blue-bright)}
  .list--process li{line-height:11px;margin-bottom:7px}
  .list--process li::before{top:2px}
  .brand-name{font-family:"Marcellus SC",serif;color:var(--blue-mid);text-align:center}
  .brand-dot{display:block;margin:0 auto 4px;width:22px;height:22px;background:var(--blue-bright)}
  .contact{font-size:9px;line-height:14px;text-align:center;white-space:nowrap}
  .contact svg{width:8px;height:8px;vertical-align:-1px;margin-right:3px;fill:var(--blue-bright)}
</style>
</head>
<body>

<!-- OUTSIDE SHEET -->
<section class="sheet sheet--outside">
  <svg class="art" viewBox="0 0 703 547">
    <defs>
      <linearGradient id="darkBg" x1="0" y1="0" x2="1" y2="1">
        <stop offset="0" stop-color="#3b3b3e"/><stop offset="1" stop-color="#222224"/>
      </linearGradient>
      <linearGradient id="bandBlue" x1="0" y1="0" x2="0" y2="1">
        <stop offset="0" stop-color="#0b3c82"/><stop offset="1" stop-color="#1b82d4"/>
      </linearGradient>
      <linearGradient id="deskPhoto" x1="0" y1="0" x2="1" y2="1">
        <stop offset="0" stop-color="#b8c7d8"/><stop offset=".5" stop-color="#eef1f5"/><stop offset="1" stop-color="#7aa6d0"/>
      </linearGradient>
      <linearGradient id="meetingPhoto" x1="0" y1="0" x2="1" y2="1">
        <stop offset="0" stop-color="#d9b07a"/><stop offset=".55" stop-color="#efe6d8"/><stop offset="1" stop-color="#9a7650"/>
      </linearGradient>
    </defs>
    <rect width="703" height="547" fill="url(#darkBg)"/>
    <path d="M0 0 L250 0 C170 8 80 20 0 40 Z" fill="var(--blue-bright)"/>
    <path d="M0 348 C80 340 180 342 240 326 L240 547 L0 547 Z" fill="url(#meetingPhoto)" role="img" aria-label="Photo: business people meeting at a desk with laptop, papers and coffee cups"/>
    <path d="M410 0 C395 150 400 400 440 547 L703 547 L703 0 Z" fill="var(--paper)"/>
    <path d="M428 80 C520 70 620 55 703 38 L703 320 C620 335 520 330 436 318 C418 240 416 160 428 80 Z" fill="url(#deskPhoto)" role="img" aria-label="Photo: hands working with a calculator, pen, charts and keyboard"/>
    <path d="M416 52 C500 44 600 40 703 35 L703 45 C600 52 500 60 418 70 Z" fill="var(--blue-bright)"/>
    <path d="M432 300 C520 330 620 320 703 298 L703 445 C600 462 500 455 440 440 C434 400 431 350 432 300 Z" fill="url(#bandBlue)"/>
    <path d="M445 547 C500 526 600 518 703 518 L703 528 C610 529 540 536 505 547 Z" fill="var(--ink-mid)"/>
    <path d="M505 547 C540 536 610 529 703 528 L703 540 C650 540 610 543 590 547 Z" fill="var(--blue-bright)"/>
  </svg>

  <!-- left panel -->
  <div class="t caps light" style="left:22px;top:48px;font-size:22px">Here to Simplify</div>
  <div class="t caps blue" style="left:22px;top:72px;font-size:14px">the Bookkeeping Process</div>
  <div class="pill" style="left:0;top:103px;width:175px;height:32px;font-size:19px">What We Do</div>
  <p class="t body-copy light" style="left:23px;top:152px;width:203px">Allow business owners to spend more time focusing on their core business by providing comprehensive bookkeeping and business consulting services. We provide the financial data and tools that allow businesses to maximize profitability and focus on growth and other areas of their business. We consider our business to be an extension of your business and look forward to the opportunity to exceed your expectations.</p>
  <div class="t blue" style="left:23px;top:279px;font-size:12px;font-weight:700">Let’s talk!</div>
  <div class="t light" style="left:23px;top:303px;font-size:10px">Schedule a no-obligation consultation today!</div>

  <!-- middle panel -->
  <div class="t" style="left:245px;top:312px;width:160px">
    <span class="brand-dot"></span>
    <div class="brand-name" style="font-size:15px;color:var(--blue-bright)">HL&amp;A</div>
    <div class="caps blue" style="text-align:center;font-size:8.5px;font-weight:700;margin-top:8px;white-space:nowrap">Halvick Ledgers &amp; Advisory</div>
    <div class="contact light" style="margin-top:7px">
      <div><svg viewBox="0 0 10 10"><path d="M5 0a3.5 3.5 0 0 0-3.5 3.5C1.5 6 5 10 5 10s3.5-4 3.5-6.5A3.5 3.5 0 0 0 5 0zm0 5a1.5 1.5 0 1 1 0-3 1.5 1.5 0 0 1 0 3z"/></svg>Brookmere Valley, PA</div>
      <div><svg viewBox="0 0 10 10"><path d="M2 0l2 2.5-1 1.2a6 6 0 0 0 3.3 3.3l1.2-1L10 8l-1.5 2C4 10 0 6 0 1.5z"/></svg>555.014.2290</div>
      <div><svg viewBox="0 0 10 10"><path d="M0 2h10v6H0z"/></svg>mara@halvickledgers.com</div>
      <div>www.halvickledgers.com</div>
    </div>
  </div>
  <div class="t blue" style="left:240px;top:489px;width:170px;text-align:center;font-size:12px;font-style:italic;line-height:14px">“It’s not just my business,<br>it’s my name.”</div>

  <!-- right panel -->
  <div class="t" style="left:565px;top:28px;width:110px">
    <span class="brand-dot" style="width:30px;height:30px"></span>
    <div class="brand-name" style="font-size:24px">HL&amp;A</div>
  </div>
  <div class="t caps" style="left:436px;top:358px;width:267px;text-align:center;color:#1b1b1b;font-size:30px;line-height:30px">Expert</div>
  <div class="t caps light" style="left:436px;top:392px;width:267px;text-align:center;font-size:16px">Bookkeeping Services</div>
  <div class="t caps" style="left:436px;top:413px;width:267px;text-align:center;color:#111;font-size:11px">for Small Bussinesses</div>
  <div class="t navy" style="left:490px;top:467px;width:200px;text-align:right;font-size:17px;line-height:21px">Trustworthy.<br>Experienced. Reliable.</div>
</section>

<!-- INSIDE SHEET -->
<section class="sheet sheet--inside">
  <svg class="art" viewBox="0 0 703 548">
    <defs>
      <linearGradient id="lowerBlue" x1="0" y1="0" x2="0" y2="1">
        <stop offset="0" stop-color="#0b3c82"/><stop offset="1" stop-color="#1c86d8"/>
      </linearGradient>
      <linearGradient id="officePhoto" x1="0" y1="0" x2="1" y2="1">
        <stop offset="0" stop-color="#c9d3de"/><stop offset=".5" stop-color="#f2f4f6"/><stop offset="1" stop-color="#4e6f95"/>
      </linearGradient>
      <linearGradient id="tabletPhoto" x1="0" y1="0" x2="1" y2="1">
        <stop offset="0" stop-color="#d8dfe7"/><stop offset=".5" stop-color="#ffffff"/><stop offset="1" stop-color="#8fb4d8"/>
      </linearGradient>
      <linearGradient id="darkBg2" x1="0" y1="0" x2="1" y2="1">
        <stop offset="0" stop-color="#3b3b3e"/><stop offset="1" stop-color="#222224"/>
      </linearGradient>
    </defs>
    <rect width="703" height="548" fill="url(#darkBg2)"/>
    <rect width="470" height="160" fill="var(--paper)"/>
    <path d="M255 84 C320 74 400 72 470 68 L470 548 L255 548 Z" fill="url(#darkBg2)"/>
    <path d="M0 150 C80 140 180 128 255 112 L255 300 C180 318 80 318 0 312 Z" fill="url(#officePhoto)" role="img" aria-label="Photo: smiling businessmen shaking hands in an office"/>
    <path d="M0 128 C90 132 180 114 255 96 L255 114 C180 132 80 146 0 150 Z" fill="var(--blue-bright)"/>
    <path d="M0 300 C80 312 180 312 255 290 L255 548 L0 548 Z" fill="url(#lowerBlue)"/>
    <rect x="468" width="235" height="96" fill="var(--blue-mid)"/>
    <path d="M468 96 L703 96 L703 292 C620 275 540 300 468 325 Z" fill="url(#tabletPhoto)" role="img" aria-label="Photo: hand pointing at charts on a tablet"/>
  </svg>

  <!-- left panel -->
  <div class="pill" style="left:0;top:20px;width:122px;height:32px;font-size:19px">Services</div>
  <div class="t caps navy" style="left:22px;top:62px;font-size:14px">Full Charge Bookkeeping</div>
  <p class="t body-copy dark" style="left:22px;top:83px;width:225px;text-align:left">We can manage all aspects of your bookkeeping and business financials and communicate to you as much and as often as you want.</p>
  <div class="t caps soft" style="left:20px;top:318px;width:205px;font-size:13px;line-height:15px">Cash Management (Bill Pay &amp; Invoicing) &amp; Vendor Management</div>
  <p class="t body-copy light" style="left:20px;top:370px;width:210px">We can handle every step from receiving bills, communicating with vendor and paying bills. We take a lot pride in helping our clients save money and one way is negotiating with vendors and finding appropriate discounts.</p>
  <div class="t caps soft" style="left:20px;top:437px;font-size:13px">Financial Statements</div>
  <p class="t body-copy light" style="left:20px;top:458px;width:210px;text-align:left">Profit and Loss – Balance Sheet – Statement of Cash Flow – Industry Specific</p>
  <p class="t body-copy light" style="left:20px;top:490px;width:210px">We accurately prepare monthly, quarterly &amp; annual financial statements in a timely manner. We also take the time to review these statements</p>

  <!-- middle panel -->
  <p class="t body-copy dark" style="left:288px;top:42px;width:175px;text-align:left">with you so that you understand the financial health of your business.</p>
  <div class="t caps blue" style="left:280px;top:86px;font-size:13px;line-height:15px">Account<br>Reconciliations</div>
  <p class="t body-copy light" style="left:272px;top:118px;width:188px;text-align:left">From bank account to credit card statements to vendor statements. We reconcile all of your accounts that impact your finances.</p>
  <div class="t caps blue" style="left:270px;top:172px;font-size:13px">Professional Liaison</div>
  <p class="t body-copy light" style="left:268px;top:194px;width:192px;text-align:left">We will work directly with your other business partners – Bankers, CPA, Insurance, Payroll, Attorney… Need a loan? We will work directly with your banker to make the process as simple as possible. Does your CPA need some data? Let us take care of that while you continue making your customers happy.</p>
  <div class="t caps blue" style="left:262px;top:296px;font-size:13px">Business Services</div>
  <ul class="t list light" style="left:266px;top:313px">
    <li>Budget</li><li>Create Proper Financial Systems</li><li>Projections</li>
  </ul>
  <div class="t caps blue" style="left:268px;top:383px;font-size:13px;line-height:15px">Why Outsource<br>Bookkeeping?</div>
  <ul class="t list light" style="left:278px;top:415px">
    <li>Save Time</li><li style="margin-left:-2px">Save Money</li><li style="margin-left:4px">Expertise</li><li style="margin-left:8px">Focused Staff</li><li style="margin-left:10px">Technology</li><li style="margin-left:14px">Experience</li>
  </ul>

  <!-- right panel -->
  <div class="t caps light" style="left:468px;top:26px;width:235px;text-align:center;font-size:15px;line-height:21px">The Financial Numbers<br><span style="font-size:19px">are the Heart Beat</span><br>of an Organization</div>
  <div class="t caps blue" style="left:480px;top:330px;font-size:13px">The Process</div>
  <ul class="t list list--process light" style="left:481px;top:354px;width:205px">
    <li>Contact Us – we like to hear from you</li>
    <li>No-Obligation Consultation</li>
    <li>Review Current Process – identify strengths and weaknesses</li>
    <li>Recommend and implement new bookkeeping process</li>
    <li>Ongoing bookkeeping partnership</li>
    <li>Provide your company with more value and service to keep earning your business (ongoing)</li>
  </ul>
</section>

</body>
</html>
```